Indy Film Production Company/Studio

We need a business card designed from an existing logo. We are a digital studio/production company that caters to creating genre entertainment, like Action, Horror, and martial arts. The card along with the logo will be used to Brand the company from letter heads to banners. The design will also be used for postcards and Brochures. It should be professional and masculine.
Updates

Thank you to all the designers who have participated. I'm narrowing down who it will be. Thank you again.

Target Market(s)

Investors, Networks, Producers, and actors

Industry/Entity Type

Film Production

Contact Information for Business Card

Teodoro Valbuena
Producer/Writer/Director
www.kestrelpicturehouse.example

Requirements
Must have
• Website address, Facebook icon and Twitter icon possibly in the back of the card.
Nice to have
• Logline of Company: Follow The Action.

```html
<!DOCTYPE html>
<html lang="en">
<head>
<meta charset="utf-8">
<title>Kestrel Picture House – Business Card</title>
<link rel="stylesheet" href="https://fonts.googleapis.com/css2?family=Open+Sans:wght@400;600;800&display=swap">
<style>
  :root {
    --backdrop: #d9d6d3;
    --card-frost: #eeeceb;
    --brand-red: #c8161d;
    --brand-red-deep: #a50f16;
    --ink-light: #f6e3e1;
    --ink-soft: #f0d2cf;
  }
  html, body {
    margin: 0;
    width: 1200px;
    height: 969px;
    overflow: hidden;
    background: var(--backdrop);
    font-family: "Open Sans", Arial, sans-serif;
  }
  .business-card {
    position: absolute;
    left: 120px;
    top: 210px;
    width: 960px;
    height: 548px;
    background: var(--card-frost);
    box-shadow: 0 10px 30px rgba(0,0,0,0.18);
    overflow: hidden;
  }
  .card-shapes {
    position: absolute;
    inset: 0;
    width: 100%;
    height: 100%;
  }
  .brand-name {
    position: absolute;
    left: 80px;
    top: 205px;
    width: 360px;
    margin: 0;
    color: var(--brand-red);
    font-weight: 800;
    text-transform: uppercase;
    line-height: 1;
  }
  .brand-name .brand-main {
    display: block;
    font-size: 74px;
    letter-spacing: 1px;
  }
  .brand-name .brand-sub {
    display: block;
    margin-top: 10px;
    font-size: 30px;
    letter-spacing: 1px;
  }
  .contact-block {
    position: absolute;
    right: 40px;
    top: 148px;
    text-align: right;
  }
  .person-name {
    margin: 0;
    font-size: 31px;
    font-weight: 400;
    color: var(--ink-light);
    text-transform: uppercase;
    letter-spacing: 0.5px;
  }
  .person-role {
    margin: 4px 0 0;
    font-size: 24px;
    font-weight: 600;
    color: var(--ink-soft);
    text-transform: uppercase;
    letter-spacing: 0.5px;
  }
  .contact-list {
    list-style: none;
    margin: 28px 0 0;
    padding: 0;
  }
  .contact-list li {
    display: flex;
    justify-content: flex-end;
    align-items: center;
    gap: 14px;
    height: 37px;
    font-size: 23px;
    color: var(--ink-light);
  }
  .contact-icon {
    width: 22px;
    height: 22px;
    flex: none;
  }
</style>
</head>
<body>
  <div class="business-card">
    <svg class="card-shapes" viewBox="0 0 960 548" preserveAspectRatio="none" aria-hidden="true">
      <polygon class="side-stripe" points="0,0 61,0 8,548 0,548" fill="var(--brand-red)"/>
      <polygon class="contact-panel" points="561,0 960,0 960,548 448,548" fill="var(--brand-red)"/>
      <polygon class="panel-shade" points="561,0 640,0 527,548 448,548" fill="var(--brand-red-deep)" opacity="0.35"/>
    </svg>

    <h1 class="brand-name">
      <span class="brand-main">Kestrel</span>
      <span class="brand-sub">Picture House</span>
    </h1>

    <div class="contact-block">
      <h2 class="person-name">Teodoro Valbuena</h2>
      <p class="person-role">Producer/Writer/Director</p>
      <ul class="contact-list">
        <li>555 014 2290
          <svg class="contact-icon" viewBox="0 0 24 24" aria-hidden="true"><path fill="var(--ink-light)" d="M6.6 10.8a15.1 15.1 0 0 0 6.6 6.6l2.2-2.2c.3-.3.7-.4 1-.2 1.1.4 2.3.6 3.6.6.6 0 1 .4 1 1V20c0 .6-.4 1-1 1A17 17 0 0 1 3 4c0-.6.4-1 1-1h3.5c.6 0 1 .4 1 1 0 1.3.2 2.5.6 3.6.1.3 0 .7-.2 1z"/></svg>
        </li>
        <li>name@kestrel.example
          <svg class="contact-icon" viewBox="0 0 24 24" aria-hidden="true"><rect x="2" y="5" width="20" height="14" fill="none" stroke="var(--ink-light)" stroke-width="2"/><polyline points="2,5 12,13 22,5" fill="none" stroke="var(--ink-light)" stroke-width="2"/></svg>
        </li>
        <li>www.kestrelpicturehouse.example
          <svg class="contact-icon" viewBox="0 0 24 24" aria-hidden="true"><circle cx="12" cy="12" r="9" fill="none" stroke="var(--ink-light)" stroke-width="2"/><ellipse cx="12" cy="12" rx="4" ry="9" fill="none" stroke="var(--ink-light)" stroke-width="1.6"/><line x1="3" y1="12" x2="21" y2="12" stroke="var(--ink-light)" stroke-width="1.6"/></svg>
        </li>
        <li>kestrelpicturehouse.example
          <svg class="contact-icon" viewBox="0 0 24 24" aria-hidden="true"><path d="M10 14a4 4 0 0 0 5.7 0l3.5-3.5a4 4 0 0 0-5.7-5.7L12 6.3" fill="none" stroke="var(--ink-light)" stroke-width="2" stroke-linecap="round"/><path d="M14 10a4 4 0 0 0-5.7 0l-3.5 3.5a4 4 0 0 0 5.7 5.7L12 17.7" fill="none" stroke="var(--ink-light)" stroke-width="2" stroke-linecap="round"/></svg>
        </li>
        <li>@kestrelpicturehouse
          <svg class="contact-icon" viewBox="0 0 24 24" aria-hidden="true"><path d="M3 4h18v12H9l-5 4v-4H3z" fill="none" stroke="var(--ink-light)" stroke-width="2" stroke-linejoin="round"/></svg>
        </li>
      </ul>
    </div>
  </div>
</body>
</html>
```